Baseball Coaching Camp for 5-14year olds needs sales campaign

Local baseball coaching camp for children is in it's 22nd year running a 4-5 week series of summer camps. Each year we use email marketing beginning around December to sell our camps to the parents to sign up their children for one or more weeks. All information about the camps can be seen on our website at https://hemmingtarn.com/. In the past we have had success by changing the look of the emails each month and offering a decreasing discount as the camps get closer.

Our target market is the parents of children ages 5-14years old who like and play baseball and are interested in improving their skills in a fun environment during the Summer months.

We would like to improve the sales by developing new creative and imaginative emails for this season. We need 6 to 8 quality ads that can somehow relate to each other , these ads will be sent via our mailing list as well as used on social media. One of the owners thought it would be nice to use the "river of lanterns" theme though we are open to all ideas.
We have given you access to a dropbox link with examples of past campaigns along with artwork and images here
https://www.filequay.net/sh/q7ptr2mzk4wnhd/BBReo-kmTulf5pLXU318jw6Hb?dl=0

```html
<!DOCTYPE html>
<html lang="en">
<head>
<meta charset="utf-8">
<title>Hemmingtarn Baseball Camps 2022</title>
<link href="https://fonts.googleapis.com/css2?family=Poppins:wght@400;500;600;700&family=Rubik:wght@400;500&display=swap" rel="stylesheet">
<style>
:root{
  --brand:#404f9e;
  --brand-dark:#33407f;
  --ink:#111111;
  --white:#ffffff;
  --footer:#050505;
  --card-line:#404f9e;
}
*{box-sizing:border-box;margin:0;padding:0}
html,body{width:1200px;height:4378px;overflow:hidden;background:var(--white)}
body{position:relative;font-family:'Rubik',sans-serif;color:var(--ink)}
.abs{position:absolute}
.wordmark{font-family:'Poppins',sans-serif;font-weight:700;color:var(--brand);letter-spacing:1px}
.header{left:0;top:0;width:1200px;height:138px;display:flex;align-items:center;justify-content:center;gap:14px}
.header .wordmark{font-size:42px}
.mark-dot{width:22px;height:22px;border-radius:50%;background:var(--brand)}

.hero{left:0;top:138px;width:1200px;height:824px;background:linear-gradient(160deg,#3c4a33 0%,#4f5a3e 30%,#6b5a45 55%,#4a3f35 80%,#3a3430 100%)}
.hero::after{content:"";position:absolute;inset:0;background:rgba(0,0,0,.35)}
.hero-title{left:112px;top:250px;font-family:'Poppins',sans-serif;font-weight:700;font-size:51px;line-height:76px;color:var(--white);z-index:2}
.hero-sub{left:110px;top:420px;font-size:22px;color:var(--white);z-index:2}
.btn{display:flex;align-items:center;justify-content:center;border-radius:40px;font-family:'Poppins',sans-serif;font-weight:500}
.btn-solid{background:var(--brand);color:var(--white)}
.hero-btn{left:112px;top:486px;width:208px;height:71px;font-size:20px;z-index:2}
.dots{left:560px;top:762px;display:flex;gap:10px;align-items:center;z-index:2}
.dot{width:14px;height:14px;border-radius:50%;background:var(--white)}
.dot.active{width:22px;height:22px;border:4px solid var(--white);background:var(--brand)}

.academy-photo{left:0;top:1042px;width:570px;height:529px;border-radius:0 50px 50px 0;background:linear-gradient(135deg,#5d6a55,#3d6bb0 45%,#d9b73a 80%,#4f5b44)}
.section-title{font-family:'Poppins',sans-serif;font-weight:500;font-size:34px;line-height:44px;letter-spacing:1px}
.academy-title{left:639px;top:1066px}
.academy-text{left:639px;top:1190px;width:490px;font-size:20px;line-height:45px}
.academy-btn{left:639px;top:1465px;width:208px;height:72px;font-size:20px}

.dates-panel{left:0;top:1651px;width:600px;height:600px;background:var(--brand);color:var(--white)}
.dates-photo{left:600px;top:1651px;width:600px;height:600px;background:linear-gradient(150deg,#3a3d40,#6b6e70 35%,#c9a23a 70%,#2f3236)}
.dates-title{position:absolute;left:112px;top:40px;font-family:'Poppins',sans-serif;font-weight:600;font-size:36px}
.week{position:absolute;left:112px;width:480px}
.week svg{position:absolute;left:0;top:4px}
.week-label{position:absolute;left:38px;top:0;font-family:'Poppins',sans-serif;font-weight:500;font-size:23px}
.week-text{position:absolute;left:38px;top:38px;width:440px;font-size:20px;line-height:30px}

.pricing-kicker{left:0;top:2322px;width:1200px;text-align:center;font-family:'Poppins',sans-serif;font-size:23px;color:var(--brand)}
.pricing-title{left:0;top:2354px;width:1200px;text-align:center;font-family:'Poppins',sans-serif;font-weight:500;font-size:36px}
.price-card{top:2448px;width:311px;height:369px;border:3px solid var(--card-line);border-radius:12px;text-align:center}
.price-name{position:absolute;left:0;top:40px;width:100%;font-family:'Poppins',sans-serif;font-size:29px;line-height:45px}
.price-value{position:absolute;left:0;top:143px;width:100%;font-family:'Poppins',sans-serif;font-weight:600;font-size:46px;color:var(--brand)}
.price-btn{position:absolute;left:50%;top:255px;margin-left:-103px;width:206px;height:67px;font-size:20px}
.btn-outline{border:2px solid var(--brand);color:var(--ink);background:var(--white)}

.promo{left:0;top:2899px;width:1200px;height:365px;background:linear-gradient(100deg,#3b4a96,#4d5ca6 40%,#44539f 70%,#3a4893);color:var(--white);text-align:center}
.promo-kicker{position:absolute;left:0;top:40px;width:100%;font-family:'Poppins',sans-serif;font-weight:500;font-size:24px}
.promo-title{position:absolute;left:0;top:88px;width:100%;font-family:'Poppins',sans-serif;font-weight:500;font-size:36px;line-height:59px}
.promo-btn{position:absolute;left:496px;top:231px;width:208px;height:71px;background:var(--white);color:var(--brand);font-size:20px}

.objectives-photo{left:0;top:3340px;width:600px;height:505px;background:linear-gradient(160deg,#7f8f4a,#a5a860 35%,#d9bf4a 60%,#3c4d2a)}
.objectives-card{left:461px;top:3415px;width:627px;height:327px;background:var(--white);box-shadow:0 4px 20px rgba(0,0,0,.18)}
.objectives-title{position:absolute;left:47px;top:52px}
.objectives-text{position:absolute;left:47px;top:122px;width:540px;font-size:20px;line-height:37px}

.footer{left:0;top:3920px;width:1200px;height:458px;background:var(--footer);color:var(--white)}
.footer .wordmark{position:absolute;left:116px;top:80px;font-size:38px;color:var(--brand)}
.footer-about{position:absolute;left:116px;top:205px;width:300px;font-size:20px;line-height:36px}
.footer-heading{position:absolute;font-family:'Poppins',sans-serif;font-weight:500;font-size:29px}
.socials{position:absolute;left:490px;top:123px;display:flex;gap:20px}
.social{width:40px;height:40px;border-radius:50%;background:var(--white)}
.contact-row{position:absolute;left:802px;font-size:20px;line-height:36px}
.contact-row svg{position:absolute;left:0;top:6px}
.contact-row span{position:absolute;left:48px;top:0;white-space:nowrap}
.copyright{position:absolute;left:0;top:398px;width:1200px;text-align:center;font-size:20px}
</style>
</head>
<body>

<header class="abs header">
  <span class="mark-dot"></span>
  <span class="wordmark">Hemmingtarn</span>
</header>

<section class="abs hero" role="img" aria-label="Photo of a young batter in a yellow jersey swinging at a pitch, catcher behind him on a baseball field"></section>
<h1 class="abs hero-title">HEMMINGTARN BASEBALL<br>CAMPS 2022</h1>
<p class="abs hero-sub">Local baseball coaching camp for children</p>
<a class="abs btn btn-solid hero-btn">GET STARTED</a>
<div class="abs dots"><span class="dot"></span><span class="dot active"></span><span class="dot"></span></div>

<div class="abs academy-photo" role="img" aria-label="Photo of a coach in a blue shirt helping a young player in a helmet with his batting stance"></div>
<h2 class="abs section-title academy-title">HEMMINGTARN BASEBALL<br>ACADEMY</h2>
<p class="abs academy-text">This is the place to be if you are looking to give your child a baseball experience second to none! This camp is geared toward baseball players ages 5 to 14 who are looking to improve their skills and knowledge of the game.</p>
<a class="abs btn btn-solid academy-btn">LEARN MORE</a>

<section class="abs dates-panel">
  <h2 class="dates-title">2022 CAMP DATES</h2>
  <div class="week" style="top:146px">
    <svg width="26" height="26" viewBox="0 0 26 26" fill="none" stroke="#fff" stroke-width="2"><circle cx="13" cy="13" r="10"/><path d="M8 13l4 4 10-11"/></svg>
    <div class="week-label">WEEK 1:</div>
    <div class="week-text">June 27 - July 1 @Ashgrove Park - Fernvale</div>
  </div>
  <div class="week" style="top:256px">
    <svg width="26" height="26" viewBox="0 0 26 26" fill="none" stroke="#fff" stroke-width="2"><circle cx="13" cy="13" r="10"/><path d="M8 13l4 4 10-11"/></svg>
    <div class="week-label">WEEK 2:</div>
    <div class="week-text">July 11 - July 15 @Corran Park-Linwick</div>
  </div>
  <div class="week" style="top:352px">
    <svg width="26" height="26" viewBox="0 0 26 26" fill="none" stroke="#fff" stroke-width="2"><circle cx="13" cy="13" r="10"/><path d="M8 13l4 4 10-11"/></svg>
    <div class="week-label">WEEK 3:</div>
    <div class="week-text">July 18 - July 22 @Ashgrove Road Park - Fernvale</div>
  </div>
  <div class="week" style="top:473px">
    <svg width="26" height="26" viewBox="0 0 26 26" fill="none" stroke="#fff" stroke-width="2"><circle cx="13" cy="13" r="10"/><path d="M8 13l4 4 10-11"/></svg>
    <div class="week-label">WEEK 4:</div>
    <div class="week-text">July 25 - July 29 @Ashgrove Road Park - Fernvale</div>
  </div>
</section>
<div class="abs dates-photo" role="img" aria-label="Photo of a young player in a red helmet and yellow jersey following through on a swing"></div>

<p class="abs pricing-kicker">PRICING</p>
<h2 class="abs pricing-title">2022 PRICING</h2>

<div class="abs price-card" style="left:107px">
  <div class="price-name">Half Day<br>(5 year olds only)</div>
  <div class="price-value">$225</div>
  <a class="btn btn-outline price-btn">See Details</a>
</div>
<div class="abs price-card" style="left:439px">
  <div class="price-name">Full Day 2<br>Week</div>
  <div class="price-value">$650</div>
  <a class="btn btn-solid price-btn">See Details</a>
</div>
<div class="abs price-card" style="left:770px">
  <div class="price-name">Full Day 3<br>Week</div>
  <div class="price-value">$925</div>
  <a class="btn btn-outline price-btn">See Details</a>
</div>

<section class="abs promo" role="img" aria-label="Blue-tinted background photo of young players at practice">
  <p class="promo-kicker">TO SAVE</p>
  <h2 class="promo-title">$25 OFF PROMOCODE<br>HAVE FUN</h2>
  <a class="btn promo-btn">SHOP NOW</a>
</section>

<div class="abs objectives-photo" role="img" aria-label="Photo of campers and a coach in a pinstriped uniform walking out of a cornfield"></div>
<div class="abs objectives-card">
  <h2 class="section-title objectives-title">CAMP OBJECTIVES</h2>
  <p class="objectives-text">HEMMINGTARN BASEBALL CAMP provides a safe, fun, and educational environment where both beginner, as well as experienced players can excel.Throughout the week, your child will learn the basic fundamentals</p>
</div>

<footer class="abs footer">
  <span class="wordmark">Hemmingtarn</span>
  <p class="footer-about">This is the place to be if you are looking to give your child a baseball experience second to none!</p>
  <h3 class="footer-heading" style="left:493px;top:62px">FOLLOW US</h3>
  <div class="socials" aria-label="Social media links">
    <span class="social"></span><span class="social"></span><span class="social"></span><span class="social"></span>
  </div>
  <h3 class="footer-heading" style="left:802px;top:56px">CONTACT US</h3>
  <div class="contact-row" style="top:122px">
    <svg width="28" height="28" viewBox="0 0 24 24" fill="#fff"><path d="M6.6 10.8a15 15 0 006.6 6.6l2.2-2.2c.3-.3.7-.4 1-.2 1.1.4 2.3.6 3.6.6.6 0 1 .4 1 1V20c0 .6-.4 1-1 1A17 17 0 013 4c0-.6.4-1 1-1h3.5c.6 0 1 .4 1 1 0 1.3.2 2.5.6 3.6.1.3 0 .7-.2 1z"/></svg>
    <span>(555) 014-2287</span>
  </div>
  <div class="contact-row" style="top:176px">
    <svg width="28" height="24" viewBox="0 0 24 20" fill="#fff"><path d="M2 2h20v2l-10 6L2 4z"/><path d="M2 6l10 6 10-6v12H2z"/></svg>
    <span>info@hemmingtarn.com</span>
  </div>
  <div class="contact-row" style="top:232px">
    <svg width="26" height="34" viewBox="0 0 24 32" fill="#fff"><path d="M12 0a10 10 0 00-10 10c0 7.5 10 22 10 22s10-14.5 10-22A10 10 0 0012 0zm0 14a4 4 0 110-8 4 4 0 010 8z"/></svg>
    <span>PO Box 48 Alderton,<br>New York 10999–0412</span>
  </div>
  <p class="copyright">©Copyrights 2021 Hemmingtarn Baseball &nbsp;|&nbsp; All Rights Reserved</p>
</footer>

</body>
</html>
```